Label design for outdoor terrace cleaner

We are Marlek Yard Living and searching for a modern, clean but colorful and exciting label packaging design. Our product is Tolvik Patio and is a weedage and terrace cleaner. It is a consumer product for webshops and retail shops, which should stand out by design and colors. We also would like it to be very visibly appealing with a photo.

Label size: 240 mm x 176 mm

Logo: MARLEK (Please adjust to any color you want)
Slogan: YARD LIVING (as part of the logo)

Label text is dutch, if you need any help with that, please ask.

Target Market(s)

Outdoor cleaning, retail market, handy shops, consumer retail market

Industry/Entity Type

Cleaning Product

Colors

Designer to choose colors to be used in the design.

Requirements
Must have
• Original ideas, marketing thoughts, some extra brainstorming for an outstanding and original result including texts, that will have consumers see our product and want to buy it. Smart use of words, photos and colors.
Nice to have
• Bright and visibly appealing colors (should include green, but nothing standard) and photo
Should not have
• Standard, dull appearance

```html
<!DOCTYPE html>
<html lang="nl">
<head>
<meta charset="utf-8">
<title>Marlek Yard Living – Tolvik Patio label</title>
<link rel="stylesheet" href="https://fonts.googleapis.com/css2?family=Poppins:wght@300;400;800&display=swap">
<style>
  :root {
    --orange: #e2712f;
    --cream: #f7ebde;
    --ink: #1d1d1b;
    --panel: rgba(250, 244, 236, 0.55);
    --leaf: rgba(150, 170, 80, 0.45);
    --sky-top: #cfd3b8;
    --sky-glow: #fbefe2;
    --hills: #a9b57a;
    --field: #8ea656;
    --deck: #d8c0ae;
  }
  * { box-sizing: border-box; margin: 0; padding: 0; }
  html, body { width: 1131px; height: 1200px; overflow: hidden; background: #ffffff; }
  body { position: relative; font-family: "Poppins", sans-serif; color: var(--ink); }

  .label {
    position: absolute; left: 40px; top: 215px; width: 1051px; height: 769px;
    overflow: hidden;
  }
  .label__photo {
    position: absolute; inset: 0;
    background:
      radial-gradient(ellipse 60% 35% at 55% 8%, var(--sky-glow) 0%, rgba(251,239,226,0) 70%),
      linear-gradient(180deg, var(--sky-top) 0%, #efe6d4 22%, var(--hills) 40%, var(--field) 58%, #b8b48c 66%, var(--deck) 72%, #cdb3a2 100%);
  }
  .label__shapes { position: absolute; inset: 0; }

  .logo {
    position: absolute; left: 28px; top: 81px; width: 470px; height: 145px;
    background: rgba(247, 240, 228, 0.6); border-radius: 8px;
    display: flex; align-items: center; justify-content: center;
  }
  .logo__name {
    font-weight: 800; font-size: 118px; line-height: 1; color: var(--orange);
    letter-spacing: -2px;
  }
  .tagline {
    position: absolute; left: 181px; top: 244px;
    background: rgba(247, 240, 228, 0.7); padding: 0 4px;
    font-weight: 400; font-size: 24px; letter-spacing: 0.5px; line-height: 30px;
  }

  .leaves { position: absolute; }
  .leaves--front { left: 170px; top: 465px; width: 230px; height: 200px; }
  .leaves--usage { left: 610px; top: 250px; width: 160px; height: 110px; }
  .leaves--notes { left: 820px; top: 500px; width: 180px; height: 110px; }

  .claims {
    position: absolute; left: 131px; top: 479px; width: 300px;
    list-style: none; text-align: center;
  }
  .claims li {
    font-weight: 300; font-size: 18.5px; letter-spacing: -0.9px;
    line-height: 44px;
  }

  .footer-line {
    position: absolute; left: 22px; top: 708px;
    color: #fff; font-size: 14.5px; font-weight: 300; line-height: 18px;
  }

  .info {
    position: absolute; left: 548px; width: 470px; height: 250px;
    background: var(--panel); border-radius: 8px;
    padding: 8px 16px 0 8px;
    font-size: 12.2px; font-weight: 300; line-height: 27.5px;
  }
  .info--usage { top: 114px; }
  .info--notes { top: 421px; padding-left: 12px; }
  .info ul { list-style: none; }
  .info li::before { content: "•"; margin: 0 8px 0 0; }
  .info--notes li { text-align: justify; }

  .caption {
    position: absolute; top: 1010px; font-size: 27px; font-weight: 400;
    transform: translateX(-50%);
  }
  .caption--front { left: 288px; }
  .caption--back { left: 794px; }
</style>
</head>
<body>
  <section class="label">
    <div class="label__photo" role="img" aria-label="Sunlit hilly green landscape above a weathered wooden terrace deck"></div>

    <svg class="label__shapes" width="1051" height="769" viewBox="0 0 1051 769" aria-hidden="true">
      <path d="M555 0 C600 60 680 40 800 40 C920 40 990 70 1051 125 L1051 0 Z" fill="var(--orange)"/>
      <path d="M0 610 C60 680 160 700 300 695 C420 690 520 690 560 730 C580 750 595 760 605 769 L0 769 Z" fill="var(--orange)"/>
    </svg>

    <div class="leaves leaves--front" role="img" aria-label="Faint green leaf decoration" style="background: radial-gradient(ellipse 45% 50% at 50% 50%, var(--leaf), rgba(150,170,80,0) 75%);"></div>
    <div class="leaves leaves--usage" role="img" aria-label="Faint green leaf decoration" style="background: radial-gradient(ellipse 45% 50% at 50% 50%, var(--leaf), rgba(150,170,80,0) 75%);"></div>
    <div class="leaves leaves--notes" role="img" aria-label="Faint green leaf decoration" style="background: radial-gradient(ellipse 45% 50% at 50% 50%, var(--leaf), rgba(150,170,80,0) 75%);"></div>

    <div class="logo"><span class="logo__name">MARLEK</span></div>
    <div class="tagline">YARD&nbsp; LIVING</div>

    <ul class="claims">
      <li>Zonder glyfosfaat</li>
      <li>Concentraat zonder giftige stoffen</li>
      <li>Resultaat binnen enkele uren</li>
      <li>Voor paden en terrassen</li>
    </ul>

    <p class="footer-line">Groen terras.<br>De must-have reiniger voor alle type terrassen, voor ieder huishouden.</p>

    <div class="info info--usage">
      <p>Useinstructions:</p>
      <ul>
        <li>Verdun het tot een 25% oplossing (bijv. 1 liter Tolvik Patio en 3 liter water).</li>
        <li>Besproei of begiet het terras met deze oplossing. 2 liter per 10 m2. (1 liter Tolvik Patio is dus voldoende voor ca. 20 m2 terras).</li>
        <li>Niet toepassen in de volle zon en als er binnen enkele uren veel neerslag wordt verwacht.</li>
        <li>Eventueel na enkele dagen het los gekomen vuil van het terras vegen of spuiten.</li>
      </ul>
    </div>

    <div class="info info--notes">
      <p>Notes:</p>
      <ul>
        <li>Op zeer hardnekkige vervuiling kan het product eventueel onverdund worden toegepast.</li>
        <li>Tolvik Patio tast bij toepassing conform de gebruiksaanwijzing gangbare buiten (natuur)steen, tegels en hout niet aan.</li>
        <li>Voorkom dat reinigingsproducten in contact komen met gewassen en/of direct in het oppervlaktewater terecht komen.</li>
        <li>Neem veiligheidsmaatregel in acht bij het werken met het onverdunde product.</li>
      </ul>
    </div>
  </section>

  <p class="caption caption--front">Front</p>
  <p class="caption caption--back">Back</p>
</body>
</html>
```